Vitamin B12 Liquid Drops Label

hi, i need a label designed for my vitamin b12 drops that i am going to be selling on shopzello. the label needs to quickly capture the attention of a buyer as he or she is scrolling through the thumbnail search results on shopzello.com my brand is called nralo. i already have an example brand logo i will be using, however, i need help designing the rest of the label. attached are some examples of labels i like for other supplements.some of these examples are pink. i do not want pink. please go for a blue/green color scheme. THE DESIGN MUST BE BOLD

Target Market(s)

adults ages 30 - 64

Font styles to use
Sans Serif

Colors
0455a3
cedeed
3176b5
85acd3
cfdeed
9bcb3b
abd037
cadf82
00a990

Requirements
Must have
• - bold design
• - somewhat gender-neutral color scheme because this will be used equally by men and women
• - B12 MUST be very prominent and visible on the label
Should not have
• - it should not be "crunchy" looking

```html
<!DOCTYPE html>
<html lang="en">
<head>
<meta charset="UTF-8">
<title>nralo B12 Drops – Label</title>
<link href="https://fonts.googleapis.com/css2?family=Mulish:wght@400;600;700;900&family=Special+Elite&display=swap" rel="stylesheet">
<style>
  :root {
    --label-bg: #2e1a45;
    --accent-teal: #1aa39a;
    --text-white: #ffffff;
    --frame-violet: #4a3368;
    --page-bg: #ffffff;
  }
  * { box-sizing: border-box; margin: 0; padding: 0; }
  html, body {
    width: 1200px; height: 1000px; overflow: hidden;
    background: var(--page-bg);
    font-family: "Mulish", sans-serif;
  }
  .label {
    position: absolute; left: 91px; top: 58px;
    width: 1018px; height: 460px;
    background: var(--label-bg);
    overflow: hidden;
    color: var(--accent-teal);
  }
  /* left panel */
  .nutrition-title {
    position: absolute; left: 53px; top: 34px;
    font-size: 17px; font-weight: 700;
  }
  .nutrition-rule {
    position: absolute; left: 52px; top: 65px;
    width: 150px; height: 4px; background: var(--accent-teal);
  }
  .nutrition-table {
    position: absolute; left: 52px; top: 81px; width: 150px;
    border: 3px solid var(--accent-teal);
  }
  .nutrition-row {
    padding: 4px 7px; font-size: 11px; font-weight: 600; line-height: 12px;
  }
  .nutrition-row + .nutrition-row { border-top: 3px solid var(--accent-teal); }
  .nutrition-row.single { padding: 7px 7px; }
  .warning {
    position: absolute; left: 58px; top: 254px; width: 180px;
  }
  .warning-head {
    font-size: 12px; letter-spacing: 0.3px; display: flex; align-items: center; gap: 6px;
  }
  .warning-text { margin-top: 6px; font-size: 13.5px; line-height: 17px; }

  /* centre panel */
  .brand-frame {
    position: absolute; left: 370px; top: 0;
    width: 278px; height: 88px;
    border: 3px solid var(--frame-violet); border-top: none;
  }
  .brand-name {
    position: absolute; left: 370px; top: 18px; width: 278px;
    text-align: center; color: var(--text-white);
    font-size: 58px; font-weight: 900; line-height: 1; letter-spacing: 1px;
  }
  .product-name {
    position: absolute; left: 370px; top: 102px;
    font-family: "Special Elite", monospace;
    color: var(--text-white); font-size: 84px; line-height: 1; font-weight: 700;
  }
  .product-form {
    position: absolute; left: 375px; top: 176px;
    font-family: "Special Elite", monospace;
    color: var(--text-white); font-size: 26px;
  }
  .drop-icon { position: absolute; left: 540px; top: 82px; }
  .pattern-area {
    position: absolute; left: 297px; top: 245px;
    width: 428px; height: 428px; border-radius: 50%;
    background: radial-gradient(circle at 50% 60%, #1f7f8a 0%, #1a9a9c 40%, #205570 80%, #2a3a5c 100%);
  }
  .volume {
    position: absolute; left: 0; top: 428px; width: 1018px;
    text-align: center; color: var(--text-white); font-size: 17px;
  }

  /* right panel */
  .info-block { position: absolute; left: 738px; width: 237px; }
  .info-block h2 {
    color: var(--text-white); font-size: 17px; font-weight: 700; margin-bottom: 6px;
  }
  .info-block p {
    font-size: 13px; line-height: 16.8px; text-align: justify; text-align-last: left;
  }
  .ingredient { top: 43px; }
  .recommendation { top: 153px; }
  .company {
    position: absolute; left: 739px; top: 304px;
    color: var(--text-white); font-size: 15.5px; line-height: 19px;
  }
  .batch-box {
    position: absolute; left: 864px; top: 355px;
    width: 112px; height: 50px;
    border: 3px solid var(--text-white);
    padding: 3px 8px; color: var(--text-white); font-size: 13px; line-height: 16px;
  }
</style>
</head>
<body>
  <section class="label">
    <h1 class="nutrition-title">Nutrition Facts</h1>
    <div class="nutrition-rule"></div>
    <div class="nutrition-table">
      <div class="nutrition-row">Lorem ipsum<br>Lorem ipsum<br>Lorem ipsum</div>
      <div class="nutrition-row single">Lorem ipsum</div>
      <div class="nutrition-row">Lorem ipsum<br>Lorem ipsum<br>Lorem ipsum<br>Lorem ipsum</div>
    </div>
    <div class="warning">
      <div class="warning-head">WARNING
        <svg width="16" height="15" viewBox="0 0 16 15" aria-hidden="true">
          <path d="M8 1 L15 14 H1 Z" fill="#1aa39a" stroke="#1aa39a" stroke-linejoin="round" stroke-width="1.5"/>
          <rect x="7.2" y="5" width="1.6" height="5" fill="#2e1a45"/>
          <rect x="7.2" y="11" width="1.6" height="1.6" fill="#2e1a45"/>
        </svg>
      </div>
      <p class="warning-text">Lorem ipsum dolor sit amet, consectetuer adipiscing elit, sed diam nonummy nibh euismod tincidunt ut laoreet dolore</p>
    </div>

    <div class="brand-frame"></div>
    <div class="brand-name">NRALO</div>
    <div class="product-name">B12</div>
    <div class="product-form">drops</div>
    <svg class="drop-icon" width="92" height="132" viewBox="0 0 92 132" aria-hidden="true">
      <defs>
        <linearGradient id="dropFill" x1="0" x2="1" y1="0" y2="0">
          <stop offset="0" stop-color="#3b2a8a"/>
          <stop offset="1" stop-color="#6a2d9a"/>
        </linearGradient>
      </defs>
      <path d="M46 0 C52 30 90 60 90 88 A44 44 0 0 1 2 88 C2 60 40 30 46 0 Z" fill="url(#dropFill)"/>
      <path d="M72 84 C76 100 70 112 60 118" stroke="#2e1a45" stroke-width="5" fill="none" stroke-linecap="round"/>
    </svg>
    <div class="pattern-area" role="img" aria-label="Decorative teal leaf pattern in a half circle"></div>
    <div class="volume">2 FL OZ (60ml)</div>

    <div class="info-block ingredient">
      <h2>Ingredient</h2>
      <p>Lorem ipsum dolor sit amet, consectetuer adipiscing elit, sed diam nonummy nibh euismod tincidunt ut laoreet</p>
    </div>
    <div class="info-block recommendation">
      <h2>Recommendation</h2>
      <p>Lorem ipsum dolor sit amet, consectetuer adipiscing elit, sed diam nonummy nibh euismod tincidunt ut laoreet</p>
    </div>
    <div class="company">Company Address<br>Made in Switzerland</div>
    <div class="batch-box">Batch:<br>Expiry Date:</div>
  </section>
</body>
</html>
```